New Business Card Design for Manufacturing

We are an engineering/manufacturing company that offers Advanced machining/assembly/engineering services, as well as innovative products for the heavy duty engine cooling markets.

We are looking to get a new business card designed that is clean and modern looking, but still fits the wide range of technical/skilled work we do.

- We hope to use this design as the base for other design work in new Presentations, web, and print work.

Industry/Entity Type

Engineering

Contact Information for Business Card

Our preferred color of blue is (RGB) 22/71/159 but can vary slightly from that color. Our content will be our Logo and full company name (Vantrell Forge Works, Inc.), company address, name, job title, phone number with extension, cell number, fax number, website, and email address on the cards.
We'd like the full company name next to the logo, but we are open to other interpretations of that layout.
Preferably, we would like the back side to be clean with just our logo, and the front to contain all of the contact information.

Colors
2f74b4
0355a3
85abd2

Requirements
Must have
• - Logo, company name, needed content - We are open to interpretation beyond that.
• - Standard size business card.
• - Horizontal orientation.
• - Enough space for lengthy names / job titles (for example, a job title could read "Directory of Human Resources" or "V.P. of Governmental Affairs"). We need this to look clean, whether the title be short (CEO) or long (as described above).

```html
<!DOCTYPE html>
<html lang="en">
<head>
<meta charset="utf-8">
<title>Vantrell Forge Works – Business Card</title>
<link href="https://fonts.googleapis.com/css2?family=Arimo:wght@400;700&display=swap" rel="stylesheet">
<style>
  :root {
    --brand-blue: #16479f;
    --ink: #2a2a2a;
    --muted-grey: #858585;
    --rule: #9a9a9a;
    --card: #ffffff;
    --backdrop: #dcc09a;
  }
  * { margin: 0; padding: 0; box-sizing: border-box; }
  html, body {
    width: 1200px;
    height: 900px;
    overflow: hidden;
    background: var(--backdrop);
    font-family: "Arimo", Arial, sans-serif;
  }
  .canvas { position: relative; width: 1200px; height: 900px; }

  .card {
    position: absolute;
    top: 330px;
    width: 420px;
    height: 240px;
    background: var(--card);
    border-radius: 20px;
    box-shadow: 3px 4px 6px rgba(0, 0, 0, 0.3);
    text-align: center;
    color: var(--ink);
  }
  .card--front { left: 155px; }
  .card--back { left: 625px; }

  .contact-name {
    position: absolute; left: 0; right: 0; top: 22px;
    font-size: 20px; line-height: 24px; font-weight: 700;
    color: var(--brand-blue);
  }
  .contact-title {
    position: absolute; left: 0; right: 0; top: 46px;
    font-size: 14px; line-height: 18px;
  }
  .divider {
    position: absolute; left: 140px; width: 140px; height: 1px;
    background: var(--rule);
  }
  .divider--top { top: 72px; }
  .divider--bottom { top: 160px; }
  .contact-lines {
    position: absolute; left: 0; right: 0; top: 81px;
    list-style: none; font-size: 14px; line-height: 18px;
  }
  .contact-lines .label { font-weight: 700; color: var(--brand-blue); }
  .address {
    position: absolute; left: 0; right: 0; top: 168px;
    font-size: 14px; line-height: 18px; font-style: normal;
  }

  .brand-name {
    position: absolute; left: 0; right: 0; top: 58px;
    font-size: 46px; line-height: 52px; font-weight: 700;
    color: var(--brand-blue); letter-spacing: 1px;
  }
  .company-name {
    position: absolute; left: 0; right: 0; top: 114px;
    font-size: 15px; line-height: 18px; font-weight: 700;
    color: var(--muted-grey); letter-spacing: 0.5px;
  }
  .website {
    position: absolute; left: 0; right: 0; top: 180px;
    font-size: 13px; line-height: 16px; font-weight: 700;
    letter-spacing: 1.4px; color: var(--brand-blue);
  }
  .website .domain { color: var(--muted-grey); }
</style>
</head>
<body>
  <div class="canvas">
    <section class="card card--front">
      <h1 class="contact-name">DANIEL MERCER</h1>
      <p class="contact-title">Managing Director</p>
      <div class="divider divider--top"></div>
      <ul class="contact-lines">
        <li><span class="label">P:</span> (044)123456789</li>
        <li><span class="label">M:</span> (044)123456789</li>
        <li><span class="label">F:</span> (044)123456789</li>
        <li><span class="label">E:</span> info@youremail.com</li>
      </ul>
      <div class="divider divider--bottom"></div>
      <address class="address">1234, Address GoesHere,<br>Country name, 12345</address>
    </section>

    <section class="card card--back">
      <p class="brand-name">VANTRELL</p>
      <p class="company-name">Vantrell Forge Works, Inc.</p>
      <p class="website">WWW.<span class="domain">WEBSITENAME</span>.COM</p>
    </section>
  </div>
</body>
</html>
```